Menu Redesign - Upscale Restaurant

We are looking to have our lunch and dinner menus redesigned. We are looking to elevate the signs some, no emojis. We want a clean but elevated look, please refer to Marlowe’s Dining Collective food menu and Vesper Tavola’s beverage menu. The company we’ve been using presented us with the attached menu / it’s filled with spelling and grammar errors.

Industry/Entity Type

Restaurant - Hospitality

```html
<!DOCTYPE html>
<html lang="en">
<head>
<meta charset="utf-8">
<title>Miss Della's Creole House — Menu</title>
<link rel="stylesheet" href="https://fonts.googleapis.com/css2?family=Gabriela&family=Marcellus&family=Montserrat:wght@600;700;800&family=Roboto+Condensed:wght@400;500&display=swap">
<style>
:root{
  --red:#d3191d;
  --red-deep:#b51217;
  --ink:#141414;
  --ink-soft:#2a2a2a;
  --cream:#f8eee1;
  --cream-warm:#f3e4d1;
  --stage:#6b6b6b;
  --text:#2d2d2d;
  --rule:#9a9a9a;
  --white:#ffffff;
}
*{box-sizing:border-box;margin:0;padding:0}
html,body{width:1200px;height:3038px;overflow:hidden}
body{background:var(--stage);position:relative;font-family:"Roboto Condensed",sans-serif;color:var(--text)}
.page{position:absolute;left:158px;width:884px;height:1320px;background:radial-gradient(ellipse at 70% 55%,var(--cream-warm),var(--cream) 60%);box-shadow:0 14px 28px rgba(0,0,0,.45);overflow:hidden}
.page--food{top:155px}
.page--drinks{top:1563px}

/* brand banner */
.brand{position:absolute;left:55px;top:0;width:220px;height:192px;filter:drop-shadow(0 6px 6px rgba(0,0,0,.3))}
.brand__shape{position:absolute;inset:0;background:var(--red);clip-path:polygon(0 0,100% 0,100% 100%,50% 84%,0 100%)}
.brand__name{position:absolute;left:0;right:0;top:52px;text-align:center;font-family:"Marcellus",serif;color:var(--white);font-size:33px;line-height:1}
.brand__sub{position:absolute;left:0;right:0;top:92px;text-align:center;font-family:"Marcellus",serif;color:var(--white);font-size:11px;letter-spacing:.12em}

/* hours */
.hours{position:absolute;left:301px;top:40px;width:256px}
.hours__title{font-family:"Gabriela",serif;color:var(--red);font-size:31px;line-height:1.1}
.hours__time{font-family:"Montserrat",sans-serif;font-weight:700;font-size:8.5px;text-transform:uppercase;color:var(--ink);margin-top:6px}
.hours__time span{color:var(--red)}
.hours__rule{height:1px;background:var(--rule);margin:6px 0 5px}
.hours__brunch{font-family:"Gabriela",serif;color:var(--red);font-size:21px;line-height:1.1}

/* section heads */
.section-head{position:absolute;left:54px;width:505px;display:flex;align-items:center;gap:8px}
.section-head__title{font-family:"Gabriela",serif;color:var(--red);font-size:30px;line-height:1;white-space:nowrap}
.section-head__band{flex:1;height:7px;background:var(--red);margin-top:8px}

/* items */
.item{position:absolute;width:240px}
.item__head{display:flex;align-items:center}
.item__name{flex:0 1 auto;min-width:0;font-family:"Montserrat",sans-serif;font-weight:800;font-size:8.2px;letter-spacing:.05em;color:var(--red);text-transform:uppercase;line-height:1.2}
.item__lead{flex:1 1 auto;min-width:8px;height:1px;background:var(--rule);margin:0 6px}
.item__note{font-family:"Montserrat",sans-serif;font-weight:700;font-size:8.5px;color:var(--red);white-space:nowrap}
.item__desc{font-size:8.3px;line-height:1.28;color:var(--text);margin-top:3px;width:200px}
.tag{flex:none;width:37px;height:12px;background:var(--ink);color:var(--white);font-family:"Montserrat",sans-serif;font-weight:700;font-size:8px;line-height:12px;text-align:center;padding-left:4px;clip-path:polygon(6px 0,100% 0,100% 100%,6px 100%,0 50%)}
.tag--red{background:var(--red)}
.tag--white{background:var(--white);color:var(--ink)}

/* dark panels */
.panel{position:absolute;left:591px;width:240px;color:var(--white)}
.panel .item__name{color:var(--white)}
.panel .item__desc{color:var(--white)}
.panel .item__lead{background:#cfcfcf}
.panel--sandwich{top:0;height:361px;background:var(--ink);clip-path:polygon(0 0,100% 0,100% calc(100% - 24px),calc(100% - 24px) 100%,24px 100%,0 calc(100% - 24px))}
.panel--salad{top:370px;height:428px;background:var(--red);clip-path:polygon(24px 0,calc(100% - 24px) 0,100% 24px,100% calc(100% - 24px),calc(100% - 24px) 100%,24px 100%,0 calc(100% - 24px),0 24px)}
.panel--spirits{top:0;height:899px;background:var(--ink);clip-path:polygon(0 0,100% 0,100% calc(100% - 26px),calc(100% - 26px) 100%,26px 100%,0 calc(100% - 26px))}
.ribbon{position:absolute;left:20px;width:196px;height:20px;background:var(--red);color:var(--white);font-family:"Montserrat",sans-serif;font-weight:800;letter-spacing:.1em;text-align:center;clip-path:polygon(0 0,100% 0,96% 50%,100% 100%,0 100%,4% 50%)}
.ribbon--small{height:14px;font-size:8px;line-height:14px;top:63px}
.ribbon--cat{font-size:12.5px;line-height:20px}
.vertical-title{position:absolute;font-family:"Marcellus",serif;color:var(--white);writing-mode:vertical-rl;transform:rotate(180deg);line-height:1}
.panel--sandwich .vertical-title{left:20px;top:87px;font-size:37px}
.panel--sandwich .item{left:71px;width:145px}
.panel--sandwich .item__desc{width:118px}
.panel__title{position:absolute;left:0;right:0;text-align:center;font-family:"Marcellus",serif;color:var(--white);line-height:1}
.panel--salad .panel__title{top:24px;font-size:38px}
.panel--salad .item{left:20px;width:196px}
.panel--salad .item__desc{width:150px}
.salad-extras{position:absolute;left:0;right:0;bottom:0;height:77px;background:var(--ink);padding:9px 30px 0;font-size:8px;line-height:1.3}
.salad-extras p+p{margin-top:8px}

/* sides */
.sides{position:absolute;left:54px;top:1106px;width:774px;height:150px;display:flex;clip-path:polygon(18px 0,calc(100% - 18px) 0,100% 18px,100% calc(100% - 18px),calc(100% - 18px) 100%,18px 100%,0 calc(100% - 18px),0 18px)}
.sides__label{width:65px;background:var(--red);position:relative}
.sides__label .vertical-title{left:14px;top:24px;font-size:36px}
.sides__col{padding-top:24px}
.sides__col--a{width:199px;background:var(--ink);padding-left:12px;padding-right:16px}
.sides__col--b{width:271px;background:var(--ink-soft);padding-left:47px;padding-right:52px}
.sides__col--c{flex:1;background:var(--ink);padding-left:30px;padding-right:39px}
.side{display:flex;align-items:center;height:22px}
.side__name{font-family:"Montserrat",sans-serif;font-weight:800;font-size:8.4px;letter-spacing:.06em;color:var(--white);line-height:1.15;white-space:nowrap}
.side__lead{flex:1;min-width:6px;height:1px;background:#777;margin:0 4px}
.side__price{font-family:"Montserrat",sans-serif;font-weight:700;font-size:9px;color:var(--red)}
.policy{position:absolute;left:589px;top:1036px;width:230px;font-size:7.6px;line-height:1.3;color:var(--red)}
.allergy{position:absolute;left:0;right:0;top:1268px;text-align:center;font-family:"Montserrat",sans-serif;font-weight:700;font-size:8px;color:var(--ink)}

/* spirits */
.panel--spirits .panel__title{top:58px;font-size:38px}
.spirit-list{position:absolute;left:25px;width:205px;display:grid;grid-template-columns:105px 100px;font-size:13px;line-height:24.8px;color:var(--white);white-space:nowrap}

/* wine */
.wine{position:absolute;left:60px;top:950px;width:498px;height:197px;background:var(--red);clip-path:polygon(20px 0,calc(100% - 20px) 0,100% 20px,100% calc(100% - 20px),calc(100% - 20px) 100%,20px 100%,0 calc(100% - 20px),0 20px);color:var(--white)}
.wine__head{height:50px;background:#1a0a0a;font-family:"Marcellus",serif;font-size:30px;line-height:54px;text-align:center}
.wine__col{position:absolute;top:88px;width:120px}
.wine__col--a{left:28px}.wine__col--b{left:182px}.wine__col--c{left:352px}
.wine__divider{position:absolute;top:90px;width:1px;height:86px;background:rgba(255,255,255,.45)}
.wine__col .item__head .item__name{color:var(--white);font-size:8.2px}
.wine__sub{font-family:"Montserrat",sans-serif;font-weight:800;font-size:8.5px;letter-spacing:.07em;margin-top:10px}
.wine__list{font-size:8.2px;line-height:15.5px;margin-top:2px}
.wine__col--b .wine__list,.wine__col--c .wine__list{margin-top:6px}

/* beers */
.beers{position:absolute;left:589px;top:962px;width:239px}
.beers__title{font-family:"Gabriela",serif;color:var(--red);font-size:30px;line-height:1}
.beers__sub{font-family:"Montserrat",sans-serif;font-weight:800;font-size:9px;letter-spacing:.07em;color:var(--red);margin-top:14px}
.beer{display:flex;align-items:center;height:16.5px}
.beer__name{font-size:8.2px;color:var(--ink);white-space:nowrap}
.beer .item__lead{margin:0 5px}

/* footer */
.footer{position:absolute;left:0;right:0;top:1218px;bottom:0;background:var(--ink)}
.footer__note{position:absolute;left:0;right:0;top:38px;text-align:center;font-family:"Montserrat",sans-serif;font-weight:600;font-size:8.5px;line-height:1.45;color:var(--white)}
.contact{position:absolute;left:58px;top:1200px;width:791px;height:31px;background:var(--red);border-radius:3px;display:flex;align-items:center;justify-content:center;gap:22px;font-family:"Montserrat",sans-serif;font-weight:700;font-size:13.5px;color:var(--white)}
</style>
</head>
<body>

<!-- FOOD PAGE -->
<section class="page page--food">
  <div class="brand"><div class="brand__shape"></div><div class="brand__name">Miss Della's</div><div class="brand__sub">CREOLE HOUSE</div></div>
  <div class="hours">
    <div class="hours__title">Happy hour food<br>&amp; drinks</div>
    <div class="hours__time">Monday to Friday <span>3:00PM-6:00PM</span></div>
    <div class="hours__rule"></div>
    <div class="hours__brunch">Brunch</div>
    <div class="hours__time">Saturday &amp; Sunday <span>11:00AM-3:30PM</span></div>
  </div>

  <div class="section-head" style="top:190px"><span class="section-head__title">Small plates</span><span class="section-head__band"></span></div>

  <div class="item" style="left:54px;top:257px"><div class="item__head"><span class="item__name">Creole Wings</span><span class="item__lead"></span><span class="tag">$16</span></div><p class="item__desc">Fried crispy bone-in traditional wings tossed in your choice of our signature sauces: Plain, Mambo, Voodoo, Hot honey lemon pepper.</p></div>
  <div class="item" style="left:54px;top:312px"><div class="item__head"><span class="item__name">Spinach Dip</span><span class="item__lead"></span><span class="tag tag--red">$13</span></div><p class="item__desc">Fresh chopped spinach cooked in a four cheese blend served with fresh tortilla chips. Add Jumbo Lump Crab +$6.</p></div>
  <div class="item" style="left:54px;top:369px"><div class="item__head"><span class="item__name">Fried Green Tomatoes</span><span class="item__lead"></span><span class="tag">$16</span></div><p class="item__desc">Sliced green tomatoes seasoned in house blend battered in panko bread crumb. Add Jumbo Lump Crab +$6.</p></div>
  <div class="item" style="left:54px;top:427px"><div class="item__head"><span class="item__name">Seafood Rolls</span><span class="item__lead"></span><span class="tag tag--red">$13</span></div><p class="item__desc">Chopped shrimp, crab meat and cheese in a egg roll served with remoulade dipping.</p></div>
  <div class="item" style="left:54px;top:474px"><div class="item__head"><span class="item__name">Steak &amp; Cheese Rolls</span><span class="item__lead"></span><span class="tag">$16</span></div><p class="item__desc">Fried crispy bone-in trad Philly steak, onions, peppers, and cheese in a egg roll served with chipotle mayo dipping.itional wings tossed in your choice of our signature sauces: Plain, Mambo, Voodoo, Hot honey lemon pepper.</p></div>
  <div class="item" style="left:54px;top:555px"><div class="item__head"><span class="item__name">Bayou Rolls</span><span class="item__lead"></span><span class="tag tag--red">$16</span></div><p class="item__desc">Diced chicken, peppers and cheese stuffed in a egg roll served with remoulade dipping.</p></div>
  <div class="item" style="left:54px;top:603px"><div class="item__head"><span class="item__name">Fried Devil Eggs</span><span class="item__lead"></span><span class="tag">$16</span></div><p class="item__desc">Sweet relish, spiced whipped eggs with a choice of being topped with fresh Jumbo Lump Crab Meat or Shrimp for a upcharge.</p></div>
  <div class="item" style="left:54px;top:662px"><div class="item__head"><span class="item__name">Hot Honey Salmon Bites</span><span class="item__lead"></span><span class="tag tag--red">$16</span></div><p class="item__desc">Deep-fried salmon tossed in hot honey sauce.</p></div>
  <div class="item" style="left:54px;top:702px"><div class="item__head"><span class="item__name">Stuffed Shrimp</span><span class="item__lead"></span><span class="tag">$16</span></div><p class="item__desc">Shrimp stuffed with jumbo lump crab meat coated in house batter, fried golden brown, over a bed jalapeño corn succotash.</p></div>

  <div class="item" style="left:318px;top:257px"><div class="item__head"><span class="item__name">Seafood Basket</span><span class="item__lead"></span><span class="tag">$16</span></div><p class="item__desc">Choice of fresh battered catfish or fried golden shrimp with season fries.</p></div>
  <div class="item" style="left:318px;top:308px"><div class="item__head"><span class="item__name">New Orleans Shrimp</span><span class="item__lead"></span><span class="tag tag--red">$13</span></div><p class="item__desc">Creamy garlic cajun sauteed shrimp served with toasted bread.</p></div>
  <div class="item" style="left:318px;top:361px"><div class="item__head"><span class="item__name">Voodoo Shrimp</span><span class="item__lead"></span><span class="tag">$16</span></div><p class="item__desc">Fried shrimp tossed in voodoo sauce topped with fresh jalapenos and blue cheese crumble.</p></div>
  <div class="item" style="left:318px;top:415px"><div class="item__head"><span class="item__name">Cup of Gumbo $15</span><span class="item__lead"></span><span class="tag tag--red">$13</span></div><p class="item__desc">Andouille sausage, shrimp, chicken slow cooked in a cajun broth topped with rice</p></div>
  <div class="item" style="left:318px;top:470px"><div class="item__head"><span class="item__name">Raw Oysters</span><span class="item__lead"></span><span class="tag">$16</span></div><p class="item__desc">Fresh shucked blue point oysters served over ice with fresh lemons, horseradish, hot sauce, and mignonette.</p></div>
  <div class="item" style="left:318px;top:525px"><div class="item__head"><span class="item__name">Chargrilled Oysters</span><span class="item__lead"></span><span class="tag tag--red">$16</span></div><p class="item__desc">Fresh shucked blue point oysters grilled with Cajun garlic butter and four cheese blend.</p></div>
  <div class="item" style="left:318px;top:578px"><div class="item__head"><span class="item__name">Rockefeller Oysters</span><span class="item__lead"></span><span class="tag">$16</span></div><p class="item__desc">Fresh shucked blue point oysters stuffed with creamy spinach and cheese</p></div>
  <div class="item" style="left:318px;top:634px"><div class="item__head"><span class="item__name">Jambalaya Oysters</span><span class="item__lead"></span><span class="tag tag--red">$16</span></div><p class="item__desc">Fresh shucked blue point oysters stuffed with creamy cajun shrimp and crab</p></div>
  <div class="item" style="left:318px;top:688px"><div class="item__head"><span class="item__name">Make it a Platter</span><span class="item__lead"></span><span class="tag">$16</span></div><p class="item__desc">(Serves 3)<br>Mix 3 of your favorite starters.<br>(Each Seafood starter added to platter are upcharged)</p></div>

  <div class="panel panel--sandwich">
    <div class="ribbon ribbon--small">ALL SERVED WITH CAJUN FRIES</div>
    <div class="vertical-title">SANDWICHES</div>
    <div class="item" style="top:85px"><div class="item__head"><span class="item__name">Loaded Burger</span><span class="item__lead"></span><span class="tag tag--white">$16</span></div><p class="item__desc">Beef patty topped with white cheddar cheese, lettuce, tomato, fried egg, and mambo sauce. Served with fries</p></div>
    <div class="item" style="top:166px"><div class="item__head"><span class="item__name">Miss Della's<br>Chicken Sandwich</span><span class="item__lead"></span><span class="tag tag--red">$16</span></div><p class="item__desc">Flash fried chicken dipped in honey garlic sauce, white cheddar cheese, lettuce, tomato, pickle served with fries</p></div>
    <div class="item" style="top:251px"><div class="item__head"><span class="item__name">Crabcake<br>Sandwich</span><span class="item__lead"></span><span class="tag tag--white">$16</span></div><p class="item__desc">Fresh jumbo lump crab cake, deep-fried or pan-seared. Topped with lettuce, tomato, crispy bacon, and remoulade sauce served with fries</p></div>
  </div>

  <div class="panel panel--salad">
    <div class="panel__title">SALADS</div>
    <div class="item" style="top:80px"><div class="item__head"><span class="item__name">Ceasar</span><span class="item__lead"></span><span class="tag tag--white">$16</span></div><p class="item__desc">Romaine, Parmesan-romano, croutons, housemade Ceasar dressing.</p></div>
    <div class="item" style="top:131px"><div class="item__head"><span class="item__name">Crispy Chicken House</span><span class="item__lead"></span><span class="tag">$16</span></div><p class="item__desc">Field greens, dried cranberries, cherry tomatoes,cucumbers, boiled egg, cheddar cheese, croutons, fried crispy chicken breast, and Housemade Champagne Vinaigrette</p></div>
    <div class="item" style="top:218px"><div class="item__head"><span class="item__name">Honey Caribbean Salmon</span><span class="item__lead"></span><span class="tag tag--white">$16</span></div><p class="item__desc">Field greens, corn off the cob,tomatoes, cucumbers,red onions, and buttermilk herb dressing</p></div>
    <div class="item" style="top:280px"><div class="item__head"><span class="item__name">Grilled Pear &amp; Walnut</span><span class="item__lead"></span><span class="tag">$16</span></div><p class="item__desc">A vibrant salad of fresh greens, charred pear slices,cucumbers, red onions, cherry tomatoes, dried cranberries, walnuts, and blackened chicken.</p></div>
    <div class="salad-extras">
      <p>Add Protein: Shrimp +7, Salmon +12, Blackened Chicken+10, Steak +16</p>
      <p>Dressing Options: Honey Mustard, Balsamic Vinaigrette, Ranch, Caesar, Blue Cheese</p>
    </div>
  </div>

  <div class="section-head" style="top:773px"><span class="section-head__title">Entrees</span><span class="section-head__band"></span></div>

  <div class="item" style="left:54px;top:831px"><div class="item__head"><span class="item__name">Crea Creole Herb Chickenole Wings</span><span class="item__lead"></span><span class="tag">$16</span></div><p class="item__desc">Creole and herb seasoned 1/2 chicken roasted tender and topped with creamy creole sauce and served with 2 sides of your choice</p></div>
  <div class="item" style="left:54px;top:887px"><div class="item__head"><span class="item__name">Creole Salmon</span><span class="item__lead"></span><span class="tag tag--red">$16</span></div><p class="item__desc">Prefectly seasoned pan-seared salmon topped with creamy creole sauce served with 2 sides of your choice. Add Crab Meat +$10</p></div>
  <div class="item" style="left:54px;top:943px"><div class="item__head"><span class="item__name">Bayou Pasta</span><span class="item__lead"></span><span class="tag">$16</span></div><p class="item__desc">House-made cream sauce, bell peppers, tomatoes, and onions over a bed of linguine pasta topped with blackened chicken breast</p></div>
  <div class="item" style="left:54px;top:1001px"><div class="item__head"><span class="item__name">Pork Chops</span><span class="item__lead"></span><span class="tag tag--red">$16</span></div><p class="item__desc">Fried or grilled pork chops smothered in southern gravy served with two sides of your choice</p></div>
  <div class="item" style="left:54px;top:1045px"><div class="item__head"><span class="item__name">Crab Cakes</span><span class="item__lead"></span><span class="tag">$16</span></div><p class="item__desc">2 Broiled crab cake, fresh jumbo lump crab meat, served with two sides.</p></div>

  <div class="item" style="left:318px;top:831px"><div class="item__head"><span class="item__name">Miss Della's Fried Chicken</span><span class="item__lead"></span><span class="tag">$16</span></div><p class="item__desc">½ chicken marinated in southern seasonings, fried golden served with two sides of your choice.</p></div>
  <div class="item" style="left:318px;top:878px"><div class="item__head"><span class="item__name">Fried Catfish</span><span class="item__lead"></span><span class="tag tag--red">$16</span></div><p class="item__desc">Catfish fried golden or blackened served with two sides of your choice</p></div>
  <div class="item" style="left:318px;top:925px"><div class="item__head"><span class="item__name">Loaded Creole Pasta</span><span class="item__lead"></span><span class="tag">$16</span></div><p class="item__desc">Sauteed shrimp, jumbo lump crab meat, and crab leg over creamy cajun linguine.</p></div>
  <div class="item" style="left:318px;top:976px"><div class="item__head"><span class="item__name">Gumbo w/ Cornbread</span><span class="item__lead"></span><span class="tag tag--red">$16</span></div><p class="item__desc">Rich Roux with chicken and veggies and seafood broth with andouille sausage, fresh shrimp, and scallion rice. Add Crab Leg</p></div>
  <div class="item" style="left:318px;top:1034px"><div class="item__head"><span class="item__name">Shrimp &amp; Grits</span><span class="item__lead"></span><span class="tag">$16</span></div><p class="item__desc">Sautéed shrimp, onions, peppers, and tomatoes in creamy cajun sauce. over cheesy grits. Add Crab Meat +$10</p></div>

  <div class="item" style="left:589px;top:831px"><div class="item__head"><span class="item__name">Red Snapper</span><span class="item__lead"></span><span class="tag">$16</span></div><p class="item__desc" style="width:210px">Choice of deep fried or roasted red snapper served with jambalaya stew sauce and two sides of your choice.</p></div>
  <div class="item" style="left:589px;top:878px"><div class="item__head"><span class="item__name">Oxtails</span><span class="item__lead"></span><span class="tag tag--red">$16</span></div><p class="item__desc" style="width:210px">Braised oxtails with butter beans Southern-style served with your choice of two sides</p></div>
  <div class="item" style="left:589px;top:925px"><div class="item__head"><span class="item__name">Catfish &amp; Grits</span><span class="item__lead"></span><span class="tag">$16</span></div><p class="item__desc" style="width:210px">Fresh wild caught blackened or fried, served over a bed of white cheddar grits topped with cajun cream sauce.Add Crab Meat +$10</p></div>
  <div class="item" style="left:589px;top:983px"><div class="item__head"><span class="item__name">Caribbean Lamb Chops</span><span class="item__lead"></span><span class="tag tag--red">$16</span></div><p class="item__desc" style="width:210px">Lamb chops seasoned to perfectation, topped with sweet caribbean glaze. Served with two sides of your choice</p></div>
  <p class="policy">Please read menu descriptions carefully and be sure about what you are ordering. All checks will have 20% gratuity added.<br>All parties 4+ will be on one check.</p>

  <div class="sides">
    <div class="sides__label"><div class="vertical-title">SIDES</div></div>
    <div class="sides__col sides__col--a">
      <div class="side"><span class="side__name">CAJUN CRAB FRIES</span><span class="side__lead"></span><span class="side__price">$18</span></div>
      <div class="side"><span class="side__name">SPINACH</span><span class="side__lead"></span><span class="side__price">$7</span></div>
      <div class="side"><span class="side__name">LEMON HERB BROCCOLINI</span><span class="side__lead"></span><span class="side__price">$9</span></div>
      <div class="side"><span class="side__name">ASPARAGU</span><span class="side__lead"></span><span class="side__price">$9</span></div>
      <div class="side"><span class="side__name">FIVE CHEESE MAC</span><span class="side__lead"></span><span class="side__price">$9</span></div>
    </div>
    <div class="sides__col sides__col--b">
      <div class="side"><span class="side__name">FRIED RICE</span><span class="side__lead"></span><span class="side__price">$8</span></div>
      <div class="side"><span class="side__name">SEAFOOD FRIED RICE</span><span class="side__lead"></span><span class="side__price">$15</span></div>
      <div class="side"><span class="side__name">MASHED POTATOES</span><span class="side__lead"></span><span class="side__price">$8</span></div>
      <div class="side"><span class="side__name">SEAFOOD MAC N CHEESE</span><span class="side__lead"></span><span class="side__price">$15</span></div>
      <div class="side"><span class="side__name">RED BEANS AND RICE</span><span class="side__lead"></span><span class="side__price">$9</span></div>
    </div>
    <div class="sides__col sides__col--c">
      <div class="side"><span class="side__name">CHEESY GRITS</span><span class="side__lead"></span><span class="side__price">$4</span></div>
      <div class="side"><span class="side__name">HONEY CORNBREAD</span><span class="side__lead"></span><span class="side__price">$6</span></div>
      <div class="side"><span class="side__name">CAJUN FRIES</span><span class="side__lead"></span><span class="side__price">$4</span></div>
      <div class="side"><span class="side__name">SWEET POTATO CASSEROLE</span><span class="side__lead"></span><span class="side__price">$7</span></div>
      <div class="side"><span class="side__name">COLLARD GREENS WITH<br>SMOKED TURKEY</span><span class="side__lead"></span><span class="side__price">$8</span></div>
    </div>
  </div>
  <p class="allergy">Please alert your server if you have any food allergies. Consuming raw or undercooked meats, poultry, seafood, shellfish or eggs may increase your risk of foodborne illness.</p>
</section>

<!-- DRINKS PAGE -->
<section class="page page--drinks">
  <div class="brand"><div class="brand__shape"></div><div class="brand__name">Miss Della's</div><div class="brand__sub">CREOLE HOUSE</div></div>
  <div class="hours">
    <div class="hours__title">Happy hour food<br>&amp; drinks</div>
    <div class="hours__time">Monday to Friday <span>3:00PM-6:00PM</span></div>
    <div class="hours__rule"></div>
    <div class="hours__brunch">Brunch</div>
    <div class="hours__time">Saturday &amp; Sunday <span>11:00AM-3:30PM</span></div>
  </div>

  <div class="section-head" style="top:220px"><span class="section-head__title">Beverages</span><span class="section-head__band"></span></div>

  <div class="item" style="left:54px;top:274px"><div class="item__head"><span class="item__name">Soft Drinks</span><span class="item__lead"></span><span class="tag">4</span></div><p class="item__desc" style="width:180px">Cola| Diet Cola| Lemon-Lime| Orange Juice| Ginger Ale| Pineapple Juice| Cranberry Juice|</p></div>
  <span class="item__note" style="position:absolute;left:240px;top:291px">(free refills)</span>
  <div class="item" style="left:54px;top:330px"><div class="item__head"><span class="item__name">Creole Lemonade &amp; Sweet Tea</span><span class="item__lead"></span><span class="tag tag--red">5</span></div><p class="item__desc">Strawberry | Peach | Mango | Watermelon | Kiwi | Blueberry</p></div>
  <div class="item" style="left:54px;top:387px"><div class="item__head"><span class="item__name">Ginger Beer</span><span class="item__lead"></span><span class="tag">4</span></div></div>

  <div class="item" style="left:318px;top:274px"><div class="item__head"><span class="item__name">Blueberry Fizz</span><span class="item__lead"></span><span class="tag">12</span></div><p class="item__desc">Blueberry, lime, ginger beer.</p></div>
  <div class="item" style="left:318px;top:317px"><div class="item__head"><span class="item__name">Pineapple Punch</span><span class="item__lead"></span><span class="tag tag--red">12</span></div><p class="item__desc">Orange &amp; pineapple juice,mai tai, peach, fresh lime.</p></div>
  <div class="item" style="left:318px;top:361px"><div class="item__head"><span class="item__name">Acqua Pura</span><span class="item__lead"></span><span class="tag">5</span></div></div>
  <div class="item" style="left:318px;top:388px"><div class="item__head"><span class="item__name">Sorgente</span><span class="item__lead"></span><span class="tag tag--red">5</span></div></div>

  <div class="section-head" style="top:447px"><span class="section-head__title">Specilaity Cocktails</span><span class="section-head__band"></span></div>

  <div class="item" style="left:54px;top:509px"><div class="item__head"><span class="item__name">Miss Della's Hurricane</span><span class="item__lead"></span><span class="tag">$16</span></div><p class="item__desc">Dark rum light, rum, passion, fruit punch lime juice, orange juice, grenadine.</p></div>
  <div class="item" style="left:54px;top:566px"><div class="item__head"><span class="item__name">Tsunami</span><span class="item__lead"></span><span class="tag tag--red">$16</span></div><p class="item__desc">Blanco tequila, pineapple, orange, passionfruit, blue curacao topped with dark tequila.</p></div>
  <div class="item" style="left:54px;top:624px"><div class="item__head"><span class="item__name">Secrets</span><span class="item__lead"></span><span class="tag">$15</span></div><p class="item__desc">Secret blend of 3 rums, tropical punch, and fresh lime</p></div>
  <div class="item" style="left:54px;top:686px"><div class="item__head"><span class="item__name">Smoked in Fashion</span><span class="item__lead"></span><span class="tag tag--red">$18</span></div><p class="item__desc">Bourbon, cubed sugar, black cherry, orange and cherry bitters.</p></div>
  <div class="item" style="left:54px;top:747px"><div class="item__head"><span class="item__name">Miskiri</span><span class="item__lead"></span><span class="tag">$18</span></div><p class="item__desc">Tequila, Grand Soleil, blackberry, pineapple, cranberry, lemon juice</p></div>
  <div class="item" style="left:54px;top:807px"><div class="item__head"><span class="item__name">Blackberry French</span><span class="item__lead"></span><span class="tag tag--red">$15</span></div><p class="item__desc">Duchess 1910 Gin, lemonade champagne, blackberries, white flower.</p></div>
  <div class="item" style="left:54px;top:867px"><div class="item__head"><span class="item__name">Margarita or Lemon Drop Flight</span><span class="item__lead"></span><span class="tag">$18</span></div><p class="item__desc">Traditional, Strawberry, Blueberry, Passionfruit, On the rocks</p></div>

  <div class="item" style="left:318px;top:509px"><div class="item__head"><span class="item__name">Lousiana Tea</span><span class="item__lead"></span><span class="tag">$15</span></div><p class="item__desc">Cousin Farley, honey mint syrup, fresh lemonade.</p></div>
  <div class="item" style="left:318px;top:561px"><div class="item__head"><span class="item__name">Pink Lady</span><span class="item__lead"></span><span class="tag tag--red">$15</span></div><p class="item__desc">Tequila, orange liqueur, lime, stawberry-kiwi, agave.</p></div>
  <div class="item" style="left:318px;top:607px"><div class="item__head"><span class="item__name">Creole Island</span><span class="item__lead"></span><span class="tag">$19</span></div><p class="item__desc">Grand Soleil, Hallard VS, tropical punch</p></div>
  <div class="item" style="left:318px;top:653px"><div class="item__head"><span class="item__name">Becky Sangria $</span><span class="item__lead"></span><span class="tag tag--red">$19</span></div><p class="item__desc">Red wine blend, Hallard VS, tropical fruit punch, and frozen popsicle.</p></div>
  <div class="item" style="left:318px;top:708px"><div class="item__head"><span class="item__name">Pineapple-Gria</span><span class="item__lead"></span><span class="tag">$19</span></div><p class="item__desc">White sparkling wine, rum, pineapple punch.</p></div>
  <div class="item" style="left:318px;top:752px"><div class="item__head"><span class="item__name">Peach Please</span><span class="item__lead"></span><span class="tag tag--red">$19</span></div><p class="item__desc">Vodka, peach nectar, champagne</p></div>
  <div class="item" style="left:318px;top:799px"><div class="item__head"><span class="item__name">Toasted Marshmallow Espresso<br>Martini</span><span class="item__lead"></span><span class="tag">$19</span></div><p class="item__desc">Toasted marshmallow, espresso, vodka, cream, white chocolate liqueur</p></div>
  <div class="item" style="left:318px;top:865px"><div class="item__head"><span class="item__name">Della's Passion</span><span class="item__lead"></span><span class="tag tag--red">$19</span></div><p class="item__desc">Duvall VSOP, orange liqueur, lemon juice, passionfruit.</p></div>

  <div class="panel panel--spirits">
    <div class="panel__title">SPIRITS</div>
    <div class="ribbon ribbon--cat" style="top:139px">BOURBON &amp; WHISKEY</div>
    <div class="spirit-list" style="top:166px"><span>Oakridge Reserve</span><span>Regal Coronet</span><span>Sage Harlan</span><span>Kilbride</span><span>Bulwark</span><span>Coronet Apple</span><span>Bulwark Rye</span><span>Hollis Creek</span><span>Tinsmith's Seal</span><span>Jeb Barrow</span><span>Cousin Farley</span></div>
    <div class="ribbon ribbon--cat" style="top:352px">SCOTCH</div>
    <div class="spirit-list" style="top:380px;grid-template-columns:205px"><span>Fergus Strand Black</span><span>Glen Aravel Dunmarran 12</span></div>
    <div class="ribbon ribbon--cat" style="top:465px">VODKA</div>
    <div class="spirit-list" style="top:493px"><span>Belvista</span><span>Silver Heron</span><span>Kettlehouse</span><span>Van Molen Double</span><span>Tomlin's</span><span>Espresso</span></div>
    <div class="ribbon ribbon--cat" style="top:598px">GIN</div>
    <div class="spirit-list" style="top:624px"><span>Madras</span><span>Tallowmere</span><span>Cobalt</span><span>Duchess</span><span>Hartwell's</span></div>
    <div class="ribbon ribbon--cat" style="top:730px">TEQUILA</div>
    <div class="spirit-list" style="top:754px"><span>Casa Amable</span><span>Espuela</span><span>Don Aurelio</span><span>Don Aurelio 1951</span><span>Marisol</span><span>Clase Celeste</span><span>Patrona</span></div>
  </div>

  <div class="wine">
    <div class="wine__head">WINE &amp; BUBBLY</div>
    <div class="wine__divider" style="left:162px"></div>
    <div class="wine__divider" style="left:333px"></div>
    <div class="wine__col wine__col--a">
      <div class="item__head"><span class="item__name">By the Glas</span><span class="item__lead" style="background:transparent"></span><span class="tag tag--white">10</span></div>
      <div class="wine__sub">REDS</div>
      <div class="wine__list">Cabernet<br>Merlot<br>Pinot Noir<br>Sweet Red Blend</div>
    </div>
    <div class="wine__col wine__col--b">
      <div class="item__head"><span class="item__name">White</span><span class="item__lead" style="background:var(--white)"></span><span class="tag">10</span></div>
      <div class="wine__list">Moscato<br>Pinot Grigio<br>Sauvignon Blanc<br>Chardonnay</div>
    </div>
    <div class="wine__col wine__col--c">
      <div class="item__head"><span class="item__name">Bubbly<br>(by the glass)</span><span class="item__lead" style="background:var(--white)"></span><span class="tag tag--white">10</span></div>
      <div class="wine__list">Prosecco 13<br>Brut 9</div>
    </div>
  </div>

  <div class="beers">
    <div class="beers__title">Beers</div>
    <div class="beers__sub">BOTTLE</div>
    <div class="beer"><span class="beer__name">Bloom Light</span><span class="item__lead"></span><span class="tag">7</span></div>
    <div class="beer"><span class="beer__name">Red Ridge</span><span class="item__lead"></span><span class="tag tag--red">7</span></div>
    <div class="beer"><span class="beer__name">Blue Harvest</span><span class="item__lead"></span><span class="tag">7</span></div>
    <div class="beer"><span class="beer__name">Costa Clara</span><span class="item__lead"></span><span class="tag tag--red">7</span></div>
    <div class="beer"><span class="beer__name">Cranky Orchard</span><span class="item__lead"></span><span class="tag">7</span></div>
    <div class="beer"><span class="beer__name">Halvorsen</span><span class="item__lead"></span><span class="tag tag--red">7</span></div>
    <div class="beer"><span class="beer__name">Seasonal IPA</span><span class="item__lead"></span><span class="tag">7</span></div>
  </div>

  <div class="footer">
    <p class="footer__note">*Please alert your server if you have any food allergies.<br>Consuming raw or undercooked meats, poultry, seafood, shellfish or eggs may increase your risk of foodborne illness.</p>
  </div>
  <div class="contact"><span>+1 555-014-7720</span><span>|</span><span>hello@missdellascreole.com</span><span>|</span><span>www.missdellascreole.com</span></div>
</section>

</body>
</html>
```